Online Training company needs a new website design (Wordpress)

We are looking for a new design for our website (run on WordPress). We currently have two websites (quizbrightly.com) and (velmoracademy.com) and are trying to combine them into a single design.

The site should contain the following sections (Start Here, courses, labs, practice exams, exam vouchers, books, articles, about us).

Start Here - With so many options on our site, we think it would be a good idea to have this page that will allow us to give students an overview of our different products/services and where to start when they first find out about our company.

Courses - These are our online video courses (products), currently hosted at velmoracademy.com. Each course has its own "product page".

Labs - These are online lab environments that a student can purchase. The layout for these would be similar to a course, but the purchase option will be different (our web developer will code all the back end stuff to make it work).

Practice Exams - This will allow students to take practice questions to study for their exams.

Exam Vouchers - Students can purchase their exam vouchers here at a discounted price for their certification exams.

Books - Will link to a page that displays our books that are available on Brixly. (Examples of the covers are attached so you can see our current designs.)

Articles - This will be our "blog" area for us to post articles each week.

About Us - A short about us page describing our company.

***
As for the design of the page itself, we like the current color scheme at velmoracademy.com, but the layout isn't working well. It was fine when we just had video courses, but as we have added new products it is becoming more and more cumbersome.

I have been looking for inspiration around the web, and saw quietharvestplan.com as a good example of trying to provide focus to new users, while breaking out various parts of a business that contains 4-6 different product lines/topics. Another example of a site we like is lessonlanternhub.com.

That said, we aren't looking to simply copy either site, and are completely open to recommendations and designs you may have.

Thank you and we look forward to working with you!

```html
<!DOCTYPE html>
<html lang="en">
<head>
<meta charset="utf-8">
<title>Quiz Brightly – Online Training</title>
<link href="https://fonts.googleapis.com/css2?family=Poppins:wght@400;500;600;700&family=Open+Sans:wght@400;600&display=swap" rel="stylesheet">
<style>
:root{
  --blue:#4a7aa8;
  --blue-dark:#3b6690;
  --blue-light:#7fa6cc;
  --ink:#1f1f1f;
  --text:#6a6a6a;
  --muted:#f3f3f3;
  --white:#ffffff;
}
*{box-sizing:border-box;margin:0;padding:0}
html,body{width:1200px;height:4147px;overflow:hidden}
body{font-family:"Open Sans",Arial,sans-serif;color:var(--text);background:var(--white);position:relative}
h1,h2,h3,h4,.nav,.btn{font-family:"Poppins",Arial,sans-serif}
.section{position:absolute;left:0;width:1200px}
.section-title{font-family:"Poppins",Arial,sans-serif;font-weight:600;font-size:30px;color:var(--ink);text-align:center;position:absolute;left:0;width:1200px}
.btn{display:inline-block;border-radius:30px;font-size:15px;font-weight:500;text-align:center;text-decoration:none}
.btn-blue{background:var(--blue);color:var(--white)}

/* hero */
.hero{top:0;height:622px;overflow:hidden}
.hero-photo{position:absolute;inset:0;background:linear-gradient(120deg,#dfe6ec 0%,#c9d5df 40%,#e8ecef 70%,#b9c8d4 100%)}
.hero-shape{position:absolute;left:0;top:0}
.brand{position:absolute;left:78px;top:42px;display:flex;align-items:center;gap:10px;font-family:"Poppins",Arial,sans-serif;font-weight:700;font-size:18px;color:var(--white);white-space:nowrap}
.brand-dot{width:34px;height:34px;border-radius:50%;border:3px solid var(--white)}
.nav{position:absolute;top:50px;left:300px;display:flex;gap:30px;font-size:14px;color:#2a2a2a;white-space:nowrap}
.nav-start{position:absolute;left:998px;top:38px;width:125px;height:46px;line-height:46px;background:var(--blue);color:var(--white);font-size:15px}
.hero-title{position:absolute;left:78px;top:280px;width:440px;font-weight:600;font-size:30px;line-height:1.35;color:var(--white)}
.hero-actions{position:absolute;left:78px;top:394px;display:flex;gap:20px}
.btn-outline{width:135px;height:44px;line-height:40px;border:2px solid var(--white);color:var(--white)}
.btn-white{width:160px;height:44px;line-height:44px;background:var(--white);color:var(--ink)}

/* welcome */
.welcome{top:622px;height:420px}
.welcome .section-title{top:62px}
.welcome-text{position:absolute;left:270px;top:118px;width:660px;text-align:center;font-size:13.5px;line-height:1.78}
.welcome .btn{position:absolute;left:528px;top:312px;width:145px;height:46px;line-height:46px}

/* courses */
.courses{top:1042px;height:498px;background:linear-gradient(180deg,#e9ecef 0%,#f4f2ef 55%,#ecebe8 100%)}
.courses .section-title{top:55px}
.course-card{position:absolute;left:185px;top:128px;width:752px;height:307px;background:var(--white);box-shadow:0 4px 18px rgba(0,0,0,.12)}
.course-info{position:absolute;left:34px;top:30px;width:340px}
.course-info h3{font-size:15px;font-weight:600;color:var(--ink);white-space:nowrap}
.course-info p{font-size:14px;line-height:1.6;margin-top:10px}
.course-price{position:absolute;left:34px;top:137px;font-family:"Poppins",Arial,sans-serif;font-weight:600;font-size:20px;color:var(--blue)}
.course-link{position:absolute;left:240px;top:142px;font-size:14px;color:var(--ink)}
.course-arrow{position:absolute;left:382px;top:33px}
.course-thumb{position:absolute;top:180px;width:180px;height:120px;background:linear-gradient(135deg,#1d2c3e,#35495f)}
.thumb-a{left:34px}
.thumb-b{left:222px}
.course-visual{position:absolute;left:408px;top:0;width:344px;height:307px;background:linear-gradient(135deg,#0f1d2b,#2a4560 60%,#1a2c40)}

/* learn */
.learn{top:1540px;height:658px}
.learn .section-title{top:56px}
.learn-intro{position:absolute;left:280px;top:120px;width:640px;text-align:center;font-size:13.5px;line-height:1.8}
.learn-photo{position:absolute;left:55px;top:205px;width:420px;height:453px;background:radial-gradient(ellipse at 45% 55%,#c9a58f 0%,#8e6a56 35%,#e7dfd8 70%,#ffffff 100%)}
.feature{position:absolute;width:320px;text-align:center}
.feature-icon{display:block;margin:0 auto 14px}
.feature h4{font-size:16px;font-weight:600;color:var(--ink)}
.feature p{font-size:13.5px;line-height:1.7;margin-top:8px}
.feature a{color:var(--blue)}
.f-videos{left:482px;top:208px}
.f-books{left:813px;top:208px}
.f-apps{left:482px;top:418px}
.f-blog{left:813px;top:418px}

/* insider */
.insider{top:2198px;height:423px;background:linear-gradient(90deg,#e8e6e0 0%,#f6f5f2 30%,#f6f5f2 70%,#e2e4e6 100%)}
.insider .section-title{top:62px}
.insider-text{position:absolute;left:300px;top:118px;width:600px;text-align:center;font-size:13.5px;line-height:1.8}
.insider-input{position:absolute;left:387px;top:196px;width:426px;height:50px;border-radius:26px;background:var(--white);box-shadow:0 2px 8px rgba(0,0,0,.08);padding-left:24px;line-height:50px;font-size:14px;font-style:italic;color:#888}
.insider-send{position:absolute;right:22px;top:16px}
.insider-note{position:absolute;left:300px;top:286px;width:600px;text-align:center;font-size:13.5px;line-height:1.8}

/* article */
.article{top:2621px;height:559px}
.article .section-title{top:58px}
.article-body{position:absolute;left:194px;top:138px;width:410px}
.article-body h3{font-size:20px;font-weight:600;color:var(--ink)}
.article-author{font-size:13.5px;margin-top:26px}
.article-body p{font-size:13.5px;line-height:1.8;margin-top:26px}
.article-body a{display:block;margin-top:22px;font-size:13.5px;line-height:1.8;color:var(--blue);text-decoration:underline}
.book-cover{position:absolute;left:763px;top:139px;width:241px;height:364px;background:var(--white);border:3px solid var(--blue)}
.book-band{height:46px;background:var(--blue);color:var(--white);font-family:"Poppins",Arial,sans-serif;font-weight:600;font-size:17px;letter-spacing:3px;text-align:center;line-height:46px}
.book-art{margin:38px auto 0;width:150px;height:130px;background:linear-gradient(160deg,#6f9bc6,#3b6690)}
.book-title{text-align:center;font-family:"Poppins",Arial,sans-serif;font-weight:700;font-size:22px;color:var(--blue-dark);margin-top:18px}
.book-author{position:absolute;bottom:14px;width:100%;text-align:center;font-family:"Poppins",Arial,sans-serif;font-weight:600;font-size:16px;color:var(--ink);letter-spacing:1px}

/* blog */
.blog{top:3180px;height:580px;background:var(--muted)}
.blog .section-title{top:62px}
.post{position:absolute;top:146px;width:263px;height:371px;background:var(--white);box-shadow:0 3px 12px rgba(0,0,0,.1)}
.post-1{left:194px}.post-2{left:484px}.post-3{left:774px}
.post-image{height:152px}
.post-1 .post-image{background:linear-gradient(135deg,#d9c9c2,#b04a4a 60%,#f1e8e4)}
.post-2 .post-image{background:linear-gradient(135deg,#b5bcc3,#5a6470 55%,#dfe2e5)}
.post-3 .post-image{background:linear-gradient(135deg,#ece7dc,#b39473 55%,#d8d4cc)}
.post-date{margin:20px 0 0 24px;font-size:12px;color:var(--ink)}
.post h4{margin:12px 24px 0;font-size:15.5px;font-weight:600;line-height:1.4;color:var(--ink)}
.post p{margin:12px 24px 0;font-size:13px;line-height:1.6}
.post-more{position:absolute;left:24px;bottom:22px;font-size:12.5px}
.post-go{position:absolute;right:24px;bottom:16px;width:40px;height:28px;background:var(--blue)}

/* partners */
.partners{top:3760px;height:153px;display:flex;justify-content:center;align-items:center;gap:72px;font-family:"Poppins",Arial,sans-serif;font-weight:600;font-size:20px;color:#8a8a8a}

/* footer */
.footer{top:3913px;height:234px;background:var(--blue);color:var(--white)}
.footer-nav{position:absolute;left:0;top:60px;width:1200px;display:flex;justify-content:center;gap:36px;font-size:14px}
.footer-nav span.sep{opacity:.8}
.footer-social{position:absolute;left:540px;top:102px;display:flex;gap:10px}
.footer-social span{width:36px;height:36px;border-radius:50%;border:2px solid var(--white)}
.footer-rule{position:absolute;left:0;top:170px;width:1200px;height:1px;background:rgba(255,255,255,.35)}
.footer-copy{position:absolute;left:0;top:190px;width:1200px;text-align:center;font-size:13.5px}
</style>
</head>
<body>

<section class="section hero">
  <div class="hero-photo" role="img" aria-label="Photo of a smiling student typing on a laptop at a desk"></div>
  <svg class="hero-shape" width="1200" height="622" viewBox="0 0 1200 622">
    <defs>
      <linearGradient id="heroBlue" x1="0" y1="0" x2="1" y2="1">
        <stop offset="0" stop-color="#5a88b5"/>
        <stop offset="1" stop-color="#3b6690"/>
      </linearGradient>
    </defs>
    <path d="M0 0 H640 C560 120 470 200 520 330 C560 440 520 540 470 622 H0 Z" fill="url(#heroBlue)" opacity=".95"/>
  </svg>
  <div class="brand"><span class="brand-dot"></span>Quiz Brightly</div>
  <nav class="nav"><span>About Us</span><span>Cources</span><span>Labs</span><span>Practice Exams</span><span>Exam Vouchers</span><span>Books</span><span>Articles</span></nav>
  <a class="btn nav-start">Start Here</a>
  <h1 class="hero-title">Learn the information. Pass the certification.</h1>
  <div class="hero-actions">
    <a class="btn btn-outline">Know More</a>
    <a class="btn btn-white">Get Free ebook</a>
  </div>
</section>

<section class="section welcome">
  <h2 class="section-title">Welcome To Quiz Brightly</h2>
  <p class="welcome-text">Marcus Hale is an assistant professor and instructor at multiple universities and colleges. He has trained thousands of students across the globe in his cyber security and information technology courses. He holds numerous information technology professional certifications including Certified Systems Defense Professional (CSDP), Certified Threat Analyst (CTA), Certified Network Guard Architect (CNGA), Digital Evidence Examiner (DEE), Digital Media Custodian (DMCU), SecureBase+, NetBase+, TechBase+, and ServiceFlow Infrastructure Library v3.</p>
  <a class="btn btn-blue">Learn More</a>
</section>

<section class="section courses">
  <h2 class="section-title">Our Cources</h2>
  <div class="course-card">
    <div class="course-info">
      <h3>ServiceFlow Foundation (Exam Voucher)</h3>
      <p>Purchase your discounted ServiceFlow Foundation exam voucher directly from Velmor Academy</p>
    </div>
    <svg class="course-arrow" width="12" height="20" viewBox="0 0 12 20"><path d="M10 2 L2 10 L10 18" fill="none" stroke="#bbb" stroke-width="2"/></svg>
    <div class="course-price">$299</div>
    <div class="course-link">View Course &nbsp;›</div>
    <div class="course-thumb thumb-a" role="img" aria-label="Course cover thumbnail for a security analyst course"></div>
    <div class="course-thumb thumb-b" role="img" aria-label="Course cover thumbnail for a project management course"></div>
    <div class="course-visual" role="img" aria-label="Course cover artwork for the ServiceFlow Foundation course"></div>
  </div>
</section>

<section class="section learn">
  <h2 class="section-title">How you can learn with us</h2>
  <p class="learn-intro">Lorem Ipsum is simply dummy text of the printing and typesetting industry. Lorem Ipsum has been the industry's standard dummy text ever since the 1500s,</p>
  <div class="learn-photo" role="img" aria-label="Photo of a student holding a tablet above a stack of books"></div>

  <div class="feature f-videos">
    <svg class="feature-icon" width="62" height="62" viewBox="0 0 62 62"><rect x="4" y="4" width="54" height="54" rx="8" fill="#4a7aa8"/><path d="M25 20 L42 31 L25 42 Z" fill="#fff"/></svg>
    <h4>Videos</h4>
    <p>Using our Quiz Brightly video series, we take complicated...<a>Read More</a></p>
  </div>
  <div class="feature f-books">
    <svg class="feature-icon" width="62" height="62" viewBox="0 0 62 62"><rect x="4" y="4" width="54" height="54" rx="8" fill="#4a7aa8"/><path d="M17 20 H29 V44 H17 Z M33 20 H45 V44 H33 Z" fill="none" stroke="#fff" stroke-width="2.5"/></svg>
    <h4>Books</h4>
    <p>Our Quiz Brightly book series will get you certified in the shortest...<a>Read More</a></p>
  </div>
  <div class="feature f-apps">
    <svg class="feature-icon" width="62" height="62" viewBox="0 0 62 62"><rect x="4" y="4" width="54" height="54" rx="8" fill="#4a7aa8"/><rect x="18" y="18" width="11" height="11" rx="2" fill="#fff"/><rect x="33" y="18" width="11" height="11" rx="2" fill="#fff"/><rect x="18" y="33" width="11" height="11" rx="2" fill="#fff"/><rect x="33" y="33" width="11" height="11" rx="2" fill="#fff"/></svg>
    <h4>Apps</h4>
    <p>Our quiz apps prepare you for the certification exam...<a>Read More</a></p>
  </div>
  <div class="feature f-blog">
    <svg class="feature-icon" width="62" height="62" viewBox="0 0 62 62"><rect x="4" y="4" width="54" height="54" rx="8" fill="#4a7aa8"/><path d="M20 16 H38 L44 22 V46 H20 Z" fill="none" stroke="#fff" stroke-width="2.5"/><path d="M26 30 H38 M26 36 H38" stroke="#fff" stroke-width="2.5"/></svg>
    <h4>Blog</h4>
    <p>Signup for your daily dose of training with our constantly...<a>Read More</a></p>
  </div>
</section>

<section class="section insider">
  <h2 class="section-title">Become A Quiz Brightly Insider</h2>
  <p class="insider-text">Join thousands of students who received our FREE eBook of ServiceFlow Foundations (Quiz Brightly) delivered right to your inbox and an exclusive special price on our video course!</p>
  <div class="insider-input">Enter e-mail*
    <svg class="insider-send" width="20" height="18" viewBox="0 0 20 18"><path d="M1 9 L19 1 L13 17 L10 10 Z" fill="#4a7aa8"/></svg>
  </div>
  <p class="insider-note">By subscribing to QUIZ BRIGHTLY Insider, you will receive a free eBook sample version of the ServiceFlow Foundations (Quiz Brightly) book with over 50 pages of excellent content including a free full practice test.</p>
</section>

<section class="section article">
  <h2 class="section-title">Get Ready To Pass With Our Latest Articles</h2>
  <div class="article-body">
    <h3>SERVICEFLOW FOUNDATION</h3>
    <div class="article-author">- MARCUS HALE</div>
    <p>Lorem Ipsum is simply dummy text of the printing and typesetting industry. Lorem Ipsum has been the industry's standard dummy text ever since the 1500s, when an unknown printer took a galley of type and scrambled it to make a type specimen book. It has survived not only five centuries, but also the leap into electronic typesetting, remaining essentially unchanged.</p>
    <a>Now available on Brixly.com in paperback and eBook formats!</a>
  </div>
  <div class="book-cover">
    <div class="book-band">QUIZ BRIGHTLY</div>
    <div class="book-art" role="img" aria-label="Cover illustration of a graduation cap"></div>
    <div class="book-title">SERVICEFLOW</div>
    <div class="book-author">MARCUS HALE</div>
  </div>
</section>

<section class="section blog">
  <h2 class="section-title">Latest Blog</h2>
  <article class="post post-1">
    <div class="post-image" role="img" aria-label="Photo of a student with a headset at a laptop"></div>
    <div class="post-date">26 jan,2018</div>
    <h4>Lorem ipsum is simply dummy text of</h4>
    <p>Lorem Ipsum is simply dummy text of the printing and</p>
    <span class="post-more">Read More</span>
    <svg class="post-go" viewBox="0 0 40 28"><rect width="40" height="28" fill="#4a7aa8"/><path d="M14 14 H26 M21 9 L26 14 L21 19" stroke="#fff" stroke-width="2" fill="none"/></svg>
  </article>
  <article class="post post-2">
    <div class="post-image" role="img" aria-label="Photo of a desk with a laptop and coffee"></div>
    <div class="post-date">26 jan,2018</div>
    <h4>Lorem ipsum is simply dummy text of</h4>
    <p>Lorem Ipsum is simply dummy text of the printing and</p>
    <span class="post-more">Read More</span>
    <svg class="post-go" viewBox="0 0 40 28"><rect width="40" height="28" fill="#4a7aa8"/><path d="M14 14 H26 M21 9 L26 14 L21 19" stroke="#fff" stroke-width="2" fill="none"/></svg>
  </article>
  <article class="post post-3">
    <div class="post-image" role="img" aria-label="Photo of a student with headphones working on a laptop"></div>
    <div class="post-date">26 jan,2018</div>
    <h4>Lorem ipsum is simply dummy text of</h4>
    <p>Lorem Ipsum is simply dummy text of the printing and</p>
    <span class="post-more">Read More</span>
    <svg class="post-go" viewBox="0 0 40 28"><rect width="40" height="28" fill="#4a7aa8"/><path d="M14 14 H26 M21 9 L26 14 L21 19" stroke="#fff" stroke-width="2" fill="none"/></svg>
  </article>
</section>

<section class="section partners">
  <span>Brixly</span>
  <span>Vidstream</span>
  <span>Learnora</span>
  <span>Linkwise Learning</span>
</section>

<footer class="section footer">
  <nav class="footer-nav">
    <span>Home</span><span class="sep">|</span><span>Support</span><span class="sep">|</span><span>Terms</span><span class="sep">|</span><span>Privacy Policy</span>
  </nav>
  <div class="footer-social"><span></span><span></span><span></span></div>
  <div class="footer-rule"></div>
  <div class="footer-copy">© QB QUIZ BRIGHTLY - 2018, All Rights Reserved.</div>
</footer>

</body>
</html>
```